Electric mountain bike tours nz

We are an Electric Mountain bike tour company in New Zealand. We will be offering bike rental and guided tours around the Nelson region in New Zealand. I want our website to represent both Mountain biking and New Zealand with the colours layout and features. We want tabs for the following:
-1 about us
-2 what we offer
-3 bookings/contact
Under the about us tab will be who we are as a a company. I want the ability to add videos to each of these tabs as we move foward with videos of the tracks we will be riding. I want the website to be editable so I can add and remove videos/photos myself. Also "our bikes" will be under this tab.
Under the what we offer tab will be
-1 bike rental and pricing
-2 guided tours and pricing
-3 recommended package deals.
I want to able to put the tracks under the guided tours tab and select beginner/ intermediate/advanced and have the tracks in each of the following to match the rider level. Also to be able to have a small video of the track would be great in this section.
Bookings and contact tab
(Further information for this tab to be updated soon)
Coded - Design and coding required
1 page
- Silver ferns, kiwi, mountains

```html
<!DOCTYPE html>
<html lang="en">
<head>
<meta charset="utf-8">
<title>Ridgeline E-Bike Tours</title>
<link rel="stylesheet" href="https://fonts.googleapis.com/css2?family=Montserrat:wght@500;600;700&family=Open+Sans:wght@400;600&display=swap">
<style>
:root{
  --ink:#1f1f1f;
  --text:#555;
  --white:#ffffff;
  --blue:#1a73e8;
  --blue-light:#2ea7f5;
  --blue-deep:#0a56c9;
  --orange:#f25a0c;
  --grey-head:#a9a9a9;
  --forest:#1b1f17;
  --footer:#e4e4e4;
  --snow:#e9eef3;
}
*{box-sizing:border-box;margin:0;padding:0}
html,body{width:1200px;height:3020px;overflow:hidden}
body{position:relative;font-family:"Open Sans",Arial,sans-serif;color:var(--text);background:var(--white)}
.abs{position:absolute}
.heading{font-family:"Montserrat",Arial,sans-serif;font-weight:600;text-transform:uppercase}
.btn{position:absolute;display:flex;align-items:center;justify-content:center;border-radius:24px;font-family:"Montserrat",Arial,sans-serif;font-weight:600;font-size:17px;color:var(--white)}
.btn-blue{background:linear-gradient(90deg,var(--blue-deep),var(--blue-light))}
.btn-outline{border:2px solid var(--white)}

/* hero */
.hero{left:0;top:0;width:1200px;height:720px;background:linear-gradient(180deg,#3a4a56 0%,#2b3128 45%,#1c2016 100%)}
.hero-photo{left:0;top:0;width:1200px;height:720px;background:radial-gradient(ellipse at 70% 75%,rgba(150,40,30,.35),transparent 40%),linear-gradient(180deg,rgba(90,110,125,.6),rgba(40,48,34,.2))}
.nav{left:0;top:14px;width:1200px;display:flex;justify-content:center;gap:52px;font-family:"Montserrat",Arial,sans-serif;font-size:15px;font-weight:500;color:var(--white)}
.nav .active{color:var(--blue-light)}
.brand{left:500px;top:92px;width:200px;height:180px;display:flex;flex-direction:column;align-items:center;justify-content:center;gap:14px}
.brand-dot{width:108px;height:108px;border-radius:50%;background:var(--white)}
.brand-name{font-family:"Montserrat",Arial,sans-serif;font-weight:700;font-size:18px;color:var(--white);text-align:center}
.hero-title{left:0;top:300px;width:1200px;text-align:center;font-size:40px;line-height:44px;color:var(--white)}
.hero-btn{left:520px;top:402px;width:168px;height:46px;border-color:var(--blue-light)}
.slider-dots{left:1074px;top:320px;display:flex;flex-direction:column;gap:9px}
.slider-dots span{width:12px;height:12px;border-radius:50%;background:var(--white)}
.slider-dots span:first-child{background:none;border:2px solid var(--white)}

/* about */
.about-bike{left:160px;top:764px;width:470px;height:330px;border-radius:40px;background:radial-gradient(ellipse at center,#8a8e92 0%,#d8d9da 60%,#fff 80%)}
.fern-left{left:120px;top:690px;width:560px;height:480px;background:radial-gradient(ellipse at 50% 50%,rgba(210,210,210,.55),transparent 65%)}
.fern-right{left:900px;top:990px;width:300px;height:190px;background:radial-gradient(ellipse at 60% 50%,rgba(210,210,210,.6),transparent 65%)}
.section-icon{width:80px;height:36px}
.about-title{left:650px;top:790px;font-size:34px;color:var(--ink)}
.lead{font-size:14px;line-height:22px}
.small{font-size:12.5px;line-height:22px}
.about-lead{left:650px;top:848px;width:380px}
.about-body{left:650px;top:902px;width:380px}

/* video */
.video-band{left:0;top:1170px;width:1200px;height:500px;background:linear-gradient(180deg,#1d7ee8 0%,#2a8ff0 40%,#1f6fd8 100%)}
.video-title{left:205px;top:1302px;font-size:28px;color:var(--white)}
.video-text{left:208px;top:1356px;width:350px;color:var(--white);font-size:12.5px;line-height:22px}
.video-btn{left:208px;top:1500px;width:170px;height:46px}
.video-frame{left:573px;top:1273px;width:466px;height:283px;background:linear-gradient(135deg,#2d2620 0%,#7a5a30 45%,#3a3a2c 100%)}
.play{left:763px;top:1373px;width:82px;height:82px;border-radius:50%;border:3px solid var(--white)}

/* packages */
.pack-band{left:0;top:1650px;width:1200px;height:700px;background:linear-gradient(180deg,#f5f7fa 0%,#dde4ec 55%,#c9d0d8 100%)}
.pack-title{left:0;top:1728px;width:1200px;text-align:center;font-size:27px;color:var(--ink)}
.kiwi{border-radius:50%;background:radial-gradient(ellipse,#7a6043 0%,#a38762 60%,transparent 72%)}
.card{position:absolute;background:var(--white);box-shadow:0 4px 16px rgba(0,0,0,.2);text-align:center}
.card-head{height:58px;display:flex;align-items:center;justify-content:center;font-family:"Montserrat",Arial,sans-serif;font-weight:600;font-size:18px;color:var(--white);text-transform:uppercase}
.card ul{list-style:none;margin:20px 24px 0}
.card li{border-bottom:1px solid #ccc;padding:7px 0;font-size:12px;color:#444}
.price{font-family:"Montserrat",Arial,sans-serif;font-size:28px;color:var(--ink);margin-top:18px}
.price small{font-size:18px}
.buy{display:inline-flex;align-items:center;justify-content:center;margin-top:10px;width:132px;height:34px;border-radius:18px;background:var(--orange);color:var(--white);font-family:"Montserrat",Arial,sans-serif;font-weight:600;font-size:13px}
.card-basic{left:212px;top:1825px;width:246px;height:350px}
.card-basic .card-head{background:var(--grey-head)}
.card-plat{left:754px;top:1825px;width:246px;height:350px}
.card-plat .card-head{background:var(--blue)}
.card-silver{left:458px;top:1793px;width:296px;height:418px;z-index:2}
.card-silver .card-head{background:linear-gradient(90deg,#1f8fec,#3fb0f8);height:64px;font-size:22px}
.card-silver ul{margin-top:22px}
.card-silver li{font-size:14px;padding:9px 0}
.card-silver .price{font-size:32px}
.card-silver .buy{width:160px;height:42px;font-size:15px;border-radius:22px}

/* booking */
.booking{left:0;top:2330px;width:1200px;height:520px;background:linear-gradient(90deg,#121410 0%,#1e2418 45%,#3a4a2a 75%,#2a3220 100%)}
.booking-photo{left:560px;top:2380px;width:640px;height:470px;background:radial-gradient(ellipse at 55% 65%,rgba(220,120,40,.45),transparent 35%),linear-gradient(180deg,#2f3d22,#5a5a3c 70%,#807058)}
.booking-title{left:218px;top:2450px;font-size:28px;color:var(--white)}
.booking-lead{left:222px;top:2504px;width:380px;color:#ddd}
.booking-body{left:222px;top:2558px;width:380px;color:#ccc}
.booking-btn{left:218px;top:2672px;width:166px;height:42px}

/* footer */
.footer{left:0;top:2840px;width:1200px;height:180px;background:var(--footer)}
.footer-brand{left:196px;top:2880px;width:120px;height:110px;display:flex;flex-direction:column;align-items:center;justify-content:center;gap:8px}
.footer-brand .brand-dot{width:54px;height:54px;background:#444}
.footer-brand .brand-name{color:#333;font-size:11px}
.footer-nav{left:350px;top:2904px;display:flex;gap:28px;font-family:"Montserrat",Arial,sans-serif;font-size:13px;font-weight:500;color:#222}
.copyright{left:350px;top:2942px;font-size:12px;color:#444}
.social{left:890px;top:2903px;display:flex;gap:6px}
.social span{width:28px;height:28px;border-radius:50%;background:#111}
</style>
</head>
<body>

<section>
  <div class="abs hero"></div>
  <div class="abs hero-photo" role="img" aria-label="Electric mountain bike parked on a ridge overlooking a bay at dusk"></div>
  <nav class="abs nav"><span class="active">HOME</span><span>ABOUT US</span><span>WHAT WE OFFER</span><span>BOOKINGS</span><span>CONTACT US</span></nav>
  <div class="abs brand"><span class="brand-dot"></span><span class="brand-name">Ridgeline E-Bike Tours</span></div>
  <h1 class="abs heading hero-title">Electric Mountain<br>Bike Tours in New Zealand</h1>
  <div class="btn btn-outline hero-btn">Click here</div>
  <div class="abs slider-dots"><span></span><span></span><span></span><span></span></div>
  <svg class="abs" style="left:0;top:610px" width="1200" height="115" viewBox="0 0 1200 115"><path d="M0 95 L120 85 L200 70 L260 90 L330 60 L420 75 L520 55 L600 40 L640 20 L690 10 L740 30 L820 20 L880 45 L960 35 L1040 60 L1120 50 L1200 70 L1200 115 L0 115Z" fill="#fff"/></svg>
</section>

<section>
  <div class="abs fern-left" role="img" aria-label="Faint silver fern decoration"></div>
  <div class="abs fern-right" role="img" aria-label="Faint silver fern decoration"></div>
  <div class="abs about-bike" role="img" aria-label="Grey electric mountain bike, side view"></div>
  <svg class="abs section-icon" style="left:658px;top:755px" viewBox="0 0 80 36"><path d="M2 34 L28 6 L40 18 L52 4 L78 34" fill="none" stroke="#1a8fe8" stroke-width="5"/></svg>
  <h2 class="abs heading about-title">About Us</h2>
  <p class="abs lead about-lead">Arnare gravida elit Integer congue augue et malesuada iaculis ipsum dui aliquet felis at cursus ma</p>
  <p class="abs small about-body">libero interdum nec interdum vel blandit sed nulla in ullamcorper est eget tempor cursus neque mi consectetuer mi a ultricies massa est sed nisl Class aptent taciti sociosqu ad litora torquent per conubia nostra per</p>
  <div class="btn btn-blue" style="left:645px;top:1012px;width:166px;height:44px">Read More</div>
</section>

<section>
  <div class="abs video-band" role="img" aria-label="Blue-toned mountain range backdrop"></div>
  <svg class="abs section-icon" style="left:208px;top:1266px" viewBox="0 0 80 36"><path d="M2 34 L28 6 L40 18 L52 4 L78 34" fill="none" stroke="#fff" stroke-width="5"/></svg>
  <h2 class="abs heading video-title">Watch Our Video</h2>
  <p class="abs video-text">penatibus et magnis dis parturient montes nascetur ridiculus mus In iaculis facilisis massa Etiam Suspendisse quam leo molestie sed luctus quis feugiat in pede Fusce tellus Sed metus augue convallis et vehicula ut pulvinar eu ante integer orci tellus</p>
  <div class="btn btn-outline video-btn">Click here</div>
  <svg class="abs" style="left:558px;top:1258px" width="496" height="313"><path d="M2 80 V2 H95" fill="none" stroke="#fff" stroke-width="3"/><path d="M400 311 H494 V230" fill="none" stroke="#fff" stroke-width="3"/></svg>
  <div class="abs video-frame" role="img" aria-label="Video still of a rider on a mountain trail at sunset"></div>
  <div class="abs play"></div>
  <svg class="abs" style="left:792px;top:1396px" width="30" height="36"><path d="M2 2 L28 18 L2 34Z" fill="#fff"/></svg>
</section>

<section>
  <div class="abs pack-band" role="img" aria-label="Snow-capped alpine peaks under a pale sky"></div>
  <svg class="abs" style="left:0;top:1640px" width="1200" height="30"><path d="M0 0 H1200 V12 L1100 20 L950 8 L800 22 L650 10 L500 24 L350 8 L200 20 L0 10Z" fill="#1f6fd8"/></svg>
  <svg class="abs section-icon" style="left:563px;top:1700px" viewBox="0 0 80 36"><path d="M2 34 L28 6 L40 18 L52 4 L78 34" fill="none" stroke="#888" stroke-width="5"/></svg>
  <h2 class="abs heading pack-title">Our Package</h2>
  <div class="abs kiwi" style="left:208px;top:1750px;width:105px;height:80px" role="img" aria-label="Kiwi bird perched on the card"></div>
  <div class="abs kiwi" style="left:1000px;top:2190px;width:160px;height:150px" role="img" aria-label="Kiwi bird standing on a ledge"></div>

  <div class="card card-basic">
    <div class="card-head">Basic</div>
    <ul><li>Praesent elementum elit at</li><li>Altricies sit amet porttitor</li><li>Mattis enim In massa</li><li>Libero interdum nec</li><li>Anterdum vel blandit sed</li></ul>
    <div class="price"><small>$</small>25.99</div>
    <div class="buy">BUY NOW</div>
  </div>
  <div class="card card-silver">
    <div class="card-head">Silver</div>
    <ul><li>Praesent elementum elit at</li><li>Altricies sit amet porttitor</li><li>Mattis enim In massa</li><li>Libero interdum nec</li><li>Anterdum vel blandit sed</li></ul>
    <div class="price"><small>$</small>45.99</div>
    <div class="buy">BUY NOW</div>
  </div>
  <div class="card card-plat">
    <div class="card-head">Platinium</div>
    <ul><li>Praesent elementum elit at</li><li>Altricies sit amet porttitor</li><li>Mattis enim In massa</li><li>Libero interdum nec</li><li>Anterdum vel blandit sed</li></ul>
    <div class="price"><small>$</small>85.99</div>
    <div class="buy">BUY NOW</div>
  </div>
</section>

<section>
  <div class="abs booking"></div>
  <div class="abs booking-photo" role="img" aria-label="Orange electric mountain bike beside a trail sign in native forest"></div>
  <svg class="abs" style="left:0;top:2300px" width="1200" height="70"><path d="M0 0 H1200 V40 L1140 30 L1080 55 L1000 38 L900 60 L820 40 L740 58 L640 35 L560 55 L460 30 L380 50 L300 34 L200 52 L110 36 L0 50Z" fill="#cbd2d9"/></svg>
  <svg class="abs section-icon" style="left:218px;top:2402px" viewBox="0 0 80 36"><path d="M2 34 L28 6 L40 18 L52 4 L78 34" fill="none" stroke="#fff" stroke-width="5"/></svg>
  <h2 class="abs heading booking-title">Our Booking</h2>
  <p class="abs lead booking-lead">Arnare gravida elit Integer congue augue et malesuada iaculis ipsum dui aliquet felis at cursus ma</p>
  <p class="abs small booking-body">libero interdum nec interdum vel blandit sed nulla in ullamcorper est eget tempor cursus neque mi consectetuer mi a ultricies massa est sed nisl Class aptent taciti sociosqu ad litora torquent per conubia nostra per</p>
  <div class="btn btn-blue booking-btn">Read More</div>
</section>

<footer>
  <div class="abs footer"></div>
  <div class="abs footer-brand"><span class="brand-dot"></span><span class="brand-name">Ridgeline E-Bike Tours</span></div>
  <nav class="abs footer-nav"><span>HOME</span><span>ABOUT US</span><span>WHAT WE OFFER</span><span>BOOKINGS</span><span>CONTACT US</span></nav>
  <p class="abs copyright">© 2018 Company Name &nbsp;All right reserved</p>
  <div class="abs social"><span></span><span></span><span></span><span></span></div>
</footer>

</body>
</html>
```